Velundra Jobs portal

Velundra Jobs is a job portal connecting job seekers and companies offering part time jobs in the Mena region, starting in the UAE. We would like to see designs that use the color blue. We have attached images to give an idea what the website should look like. When a company posts a job the job seekers are not allowed to see which company has posted a job. There should also be a coinvex gateway. On the landing page we want a catching picture that we will send.

Target Market(s)

Students and promotional workers

Logo Text

Velundra Jobs

Coding

Coded - Design and coding required

Number of Pages Required

4 page

Font styles to use
Sans Serif

Colors
33a6d7
0692cd
85cae6

```html
<!DOCTYPE html>
<html lang="en">
<head>
<meta charset="utf-8">
<title>Velundra Jobs – Job Listings</title>
<link rel="stylesheet" href="https://fonts.googleapis.com/css2?family=Roboto:ital,wght@0,300;0,400;0,500;1,400&display=swap">
<style>
:root{
  --blue:#0692cd;
  --mid:#33a6d7;
  --sky:#85cae6;
  --ink:#333;
  --muted:#666;
  --line:#e2e2e2;
  --dash:#bbb;
  --teal:#3cb8c4;
}
*{box-sizing:border-box;margin:0;padding:0}
html,body{width:1200px;height:785px;overflow:hidden;background:#fff;font-family:'Roboto',sans-serif;color:var(--ink)}
.page{position:relative;width:1200px;height:785px}
.site-header{position:absolute;left:0;top:0;width:1200px;height:97px;background:linear-gradient(#fff 40%,#e4e4e4);border-bottom:2px solid #d4d4d4}
.brand{position:absolute;left:78px;top:26px;display:flex;align-items:center;gap:10px}
.brand-dot{width:40px;height:40px;border-radius:50%;background:var(--mid)}
.brand-name{font-size:34px;font-weight:300;color:var(--teal);letter-spacing:.5px}
.main-nav{position:absolute;left:343px;top:41px;display:flex;gap:29px;font-size:13px;color:#444}
.icon{position:absolute}
.search-icon{left:866px;top:40px}
.bell-icon{left:916px;top:38px}
.badge{position:absolute;left:930px;top:33px;width:19px;height:19px;border-radius:50%;background:var(--mid);color:#fff;font-size:10px;font-weight:500;display:flex;align-items:center;justify-content:center}
.avatar{position:absolute;left:978px;top:28px;width:46px;height:46px;border-radius:50%;border:2px solid #fff;box-shadow:0 0 0 1px #ccc;background:linear-gradient(#c9b7a4,#7f8ea3)}
.btn{background:linear-gradient(var(--mid),var(--blue));color:#fff;border:none;border-radius:4px;font-family:inherit;font-weight:500;display:flex;align-items:center;justify-content:center;letter-spacing:.4px}
.login-btn{position:absolute;left:1056px;top:35px;width:71px;height:33px;font-size:12px}
.panel{position:absolute;background:#fff;border:2px solid #e6e6e6;border-radius:6px}
.categories{left:76px;top:129px;width:240px;height:341px;overflow:hidden}
.categories h2{height:40px;background:linear-gradient(var(--mid),var(--sky));color:#fff;font-size:15px;font-weight:500;padding:12px 15px;letter-spacing:.3px}
.category-list{list-style:none;padding:4px 12px 0 15px}
.category-list li{display:flex;justify-content:space-between;font-size:12.5px;height:35px;align-items:center;border-bottom:1px dashed var(--dash);padding-right:10px}
.category-list li:last-child{border-bottom:none}
.filter-bar{left:343px;top:129px;width:784px;height:84px}
.field{position:absolute;top:20px;height:39px;border:1px solid #d5d5d5;border-radius:6px;font-size:12px;font-style:italic;color:#777;padding:12px 15px}
.keyword{left:16px;width:280px}
.district{left:311px;width:280px}
.district svg{position:absolute;right:10px;top:16px}
.filter-btn{position:absolute;left:626px;top:20px;width:133px;height:39px;font-size:14px;font-weight:400}
.jobs{left:343px;top:226px;width:784px;height:245px;overflow:hidden}
.job-row{position:relative;height:50px;font-size:12.5px;color:#444}
.job-row span{position:absolute;top:50%;transform:translateY(-50%)}
.job-row .c1{left:22px}.job-row .c2{left:206px}.job-row .c3{left:408px}
.job-row .btn{position:absolute;left:648px;top:10px;width:96px;height:30px;font-size:12px}
.job-head{height:41px;background:linear-gradient(#fff,#ebebeb);color:var(--blue);font-weight:500;font-size:13px}
.job-row.active{height:54px;background:var(--sky);color:#fff}
.job-row.active .btn{top:12px}
.job-row.divided::after{content:"";position:absolute;left:16px;right:14px;bottom:0;border-bottom:1px dashed var(--dash)}
.featured-title{position:absolute;left:342px;top:511px;font-size:19px;font-weight:400;letter-spacing:.4px;color:#333}
.provider{position:absolute;top:551px;height:84px;border:2px solid #e3e3e3;display:flex;align-items:center;justify-content:center;gap:8px;font-size:22px;font-weight:500;color:#333}
.provider i{display:block;width:18px;height:18px;border-radius:50%;background:var(--mid)}
.site-footer{position:absolute;left:76px;top:716px;width:1051px;display:flex;justify-content:space-between;font-size:11px}
.copyright{color:#24509a}
.footer-nav{color:#555;display:flex;gap:6px}
</style>
</head>
<body>
<div class="page">
  <header class="site-header">
    <div class="brand"><span class="brand-dot"></span><span class="brand-name">velundra</span></div>
    <nav class="main-nav"><span>About Us</span><span>Contact Us</span></nav>
    <svg class="icon search-icon" width="24" height="24" viewBox="0 0 24 24" aria-label="Search"><circle cx="9" cy="9" r="6" fill="none" stroke="#999" stroke-width="2.5"/><path d="M13.5 13.5L21 21" stroke="#999" stroke-width="3.5" stroke-linecap="round"/></svg>
    <svg class="icon bell-icon" width="22" height="24" viewBox="0 0 22 24" aria-label="Notifications"><path d="M11 2c-4 0-6 3-6 7v5l-3 4h18l-3-4V9c0-4-2-7-6-7z" fill="#aaa"/><circle cx="11" cy="20.5" r="2.5" fill="#aaa"/></svg>
    <span class="badge">20</span>
    <div class="avatar" role="img" aria-label="User profile photo"></div>
    <button class="btn login-btn">LOG IN</button>
  </header>

  <aside class="panel categories">
    <h2>CATEGORIES</h2>
    <ul class="category-list">
      <li><span>Vestibulum ante</span><span>(23)</span></li>
      <li><span>Ipsum primis in faucibus</span><span>(23)</span></li>
      <li><span>Orci luctus et</span><span>(23)</span></li>
      <li><span>Ultrices posuere cubilia</span><span>(23)</span></li>
      <li><span>Suspendisse</span><span>(23)</span></li>
      <li><span>Etiam risus</span><span>(23)</span></li>
      <li><span>Aliquam ullamcorper</span><span>(23)</span></li>
      <li><span>Sed vel magna</span><span>(23)</span></li>
    </ul>
  </aside>

  <section class="panel filter-bar">
    <div class="field keyword">Keyword</div>
    <div class="field district">District<svg width="14" height="8" viewBox="0 0 14 8"><path d="M0 0h14L7 8z" fill="#aaa"/></svg></div>
    <button class="btn filter-btn">FILTER</button>
  </section>

  <section class="panel jobs">
    <div class="job-row job-head"><span class="c1">Job Title</span><span class="c2">Date</span><span class="c3">Provider Name</span></div>
    <div class="job-row active"><span class="c1">Job Title Gose Here</span><span class="c2">Due Date: May29, 2015</span><span class="c3">Provider Name Goes Here</span><button class="btn">APPY NOW</button></div>
    <div class="job-row divided"><span class="c1">Job Title Gose Here</span><span class="c2">Due Date: May29, 2015</span><span class="c3">Provider Name Goes Here</span><button class="btn">APPY NOW</button></div>
    <div class="job-row divided"><span class="c1">Job Title Gose Here</span><span class="c2">Due Date: May29, 2015</span><span class="c3">Provider Name Goes Here</span><button class="btn">APPY NOW</button></div>
    <div class="job-row"><span class="c1">Job Title Gose Here</span><span class="c2">Due Date: May29, 2015</span><span class="c3">Provider Name Goes Here</span><button class="btn">APPY NOW</button></div>
  </section>

  <h3 class="featured-title">FEATURED JOB PROVIDER</h3>
  <div class="provider" style="left:343px;width:185px"><i></i>Norvale</div>
  <div class="provider" style="left:543px;width:185px"><i></i>Brightwick</div>
  <div class="provider" style="left:741px;width:185px"><i></i>Tessmoor</div>
  <div class="provider" style="left:942px;width:185px"><i></i>Calderon</div>

  <footer class="site-footer">
    <span class="copyright">Copyright © 2015Velundra .All Right Reserved</span>
    <nav class="footer-nav"><span>About Us</span><span>/</span><span>Term &amp; Conditions</span><span>/</span><span>Site Map</span></nav>
  </footer>
</div>
</body>
</html>
```